Blood Testing Health App

We are looking for a graphics designer to create a web app for us so that we may insert it into a health management website system.
For branding purposes we are at www.Vantiqor.com and we are revamping our website... Example of new colors attached.
How we work...
We are a blood testing company based in the USA.
We offer a blood testing service nationwide in the USA.
We allow customers to order tests directly from us, visit a lab, have their blood drawn, or submit a urine sample, the lab tests it and they send the results back to our computer system and we share it with the customer.
The benefits of this are the customer does not need to go to the doctor and pay for the doctors visit to order these tests, which save them money. The tests are cheaper than going through the doctor. The customer simply uses us to get the test and the results and they can then take the results to their doctor... this process has saved them money. Others may be interested in regular check ups for blood work etc... and this allows them to do it with out needing a doctor, or if you have no insurance, this is a cheaper option too. We are quicker than a doctor, customers do not need appointments etc.
Hopefully you now have a better understanding as to what we do.
Here is the spec.
The app screen size is 750 px wide by 700 px high. ( A pdf is attached to show where the app is going to go, it is on page 3 of the pdf) The customer will have the ability to scroll… therefore the length of the page can be longer.
The app will consist of the following sections
Entry Page –
This will be the first page the user sees upon opening the app. This will be where they are directed from to the sections of the app discussed below. This needs to be branded for VantiQor with a modern look.
1 – Order Test (Giving them the ability to purchase a blood test within the app)
2 – VantiQor Dashboard (A dashboard that has everything they could need to use our service_
How it works Section on entry page – this will be a simple set of graphics showing how the service works. We already have the graphics for this, they do not need to be built again. They are attached to this brief
Basic structure of sections –
Order Test –
This page contains all tests, filed in categories – and Sub categories – Each test needs a link to an Information section – Price – Buy Now – Cart Process
VantiQor Dashboard –
A page of icons along the top of the app
- My Confirmation
- My Nearest Lab
- My Receipt
- My Orders
- My Account
- My Results
- My Inbox
- Contact Us
Sections in more detail -
Order A Test –
Show all categories/ sub categories – There are 23 categories, 14 sub categories, and within these categories are 300 tests - Here is the information for the categories etc - http://www.vantiqor.com/panels.aspx?PanelGroupID=4 Just in case it helps :)
We need to present this in a graphic format that is spacious, modern (brimlake, kivvo web appearance is the direction we are going for) We need it to be clear and not overwhelming to the customer.
Functionality idea…
Customer clicks category/ subcategory and tests appear.
Customer sees small 35 word description. For more information the test opens into a lightbox or expand the container which ever graphic designer believes to be most visually appealing
Buy Now must always be visible, along with price of the test
Buying process explained – Customer clicks buy now –
They are then taken to a Review Order screen ( This contains Order summary and choose payment method – insert payment details )
– Confirm payment –
Confirmation screen appears, thanking them.
They are then taken to the VantiQor Dashboard...
VantiQor Dashboard –
"My Confirmation" - Print Confirmation Order (PDF is in brief, we want this web based not a pdf download)
"My Nearest Lab Location" - This does not need to be designed because the web developer has this part under control, but we do need the icon in the dashboard
"My Receipt" - Print receipt - This does not exist in our system yet. So we need to create this from scratch - It will need to have - The test they are purchasing and the amount of the test - The customers name - The order ID - Must provide printer friendly option too
"My Orders" - This will have a list of orders - At the end of each order will be a status update of either "Test results" "Open order"
A graphic table format would be perfect. This will be linked to relevant results if they have been received. I have also attached a version of what the customer currently sees on our website. We know it is nasty ;) We are redesigning... but the information is there for this section to help design it with the right info. If the results are ready it will say in this list.
"Results Ready" will be a link to show those results once the customer has clicked the link, and the results will appear in the app, under the icons. There must be a printer friendly version too.
"My Results" Developer will sort this page out but we need the icon... It will be exactly like my orders but only show test results
"My Account" - This will be a place for them to update their personal information - Name, DOB, Address, Email Address
"My Inbox" - An inbox interface - Our way of contacting the customer for promotions we are running etc – We need a design of how this screen will appear. We also need the icon in the dashboard to have a notification on it if there are messages in the customers inbox. A little red 1, or circle with number of messages in the inbox.
"Customer Service" - This does not need to be designed because the web developer has this part under control, but we do need the icon in the dashboard
Icons appear along the top of app ( example - Mac icons/ iphone app icons) When the customer clicks an icon the content always appears below the icons
Here is more information for the icons and what should appear when each icon is clicked.
Screens to be designed –
Entry Page
Order A Test Page
Review Order Screen/Payment Screen - Show a lightbox that shows payment has been confirmed. Customer clicks close and are on the Confirmation Screen
VantiQor Dashboard - Screens mentioned in detail above
We can't wait to see your designs!
Please email any questions.
Hi all this is the first time we have used pixel harbor and understand the budget was too low for this project. We have now increased the budget to $2,000 and extended the deadline by another week
Hi all we are receiving some really great designs. I just added an example of the space that the web app will be going into... It is called "morvelapp.pdf"
Hi guys updated the brief. Hopefully this will help with the dashboard part of the design

```html
<!DOCTYPE html>
<html lang="en">
<head>
<meta charset="utf-8">
<title>VantiQor Dashboard – Sign In</title>
<link rel="stylesheet" href="https://fonts.googleapis.com/css2?family=Open+Sans:wght@400;600;700&display=swap">
<style>
  :root {
    --green: #7cc036;
    --green-dark: #6aab2b;
    --ink: #555a58;
    --ink-dark: #3f4442;
    --grey-tab: #575c59;
    --band-top: #ececec;
    --band-bottom: #dedede;
    --panel: #ebebeb;
    --field: #f4f4f4;
    --field-border: #dddddd;
    --link-red: #f03c00;
    --badge-red: #f2400f;
    --active-blue: #1a6fc4;
    --muted: #9a9a9a;
    --white: #ffffff;
  }
  * { box-sizing: border-box; margin: 0; padding: 0; }
  html, body { width: 1068px; height: 1200px; overflow: hidden; background: var(--white); }
  body { font-family: "Open Sans", Arial, sans-serif; color: var(--ink); }

  .app {
    position: absolute; left: 0; top: 0;
    width: 750px; height: 843px;
    transform: scale(1.424); transform-origin: 0 0;
  }

  /* Header */
  .site-header { position: absolute; left: 0; top: 0; width: 750px; height: 101px; background: var(--white); }
  .brand { position: absolute; left: 18px; top: 48px; display: flex; align-items: center; gap: 8px; }
  .brand-square { width: 14px; height: 14px; background: var(--green); }
  .brand-name { font-size: 38px; font-weight: 400; color: var(--ink-dark); letter-spacing: 0.5px; line-height: 1; }

  .main-tab { position: absolute; top: 29px; height: 72px; width: 124px; text-align: center; font-size: 11px; padding-top: 14px; }
  .main-tab svg { display: block; margin: 0 auto 6px; }
  .main-tab--order { left: 338px; color: var(--muted); }
  .main-tab--dashboard { left: 456px; background: var(--band-top); border-radius: 8px 8px 0 0; color: var(--green); }

  .social { position: absolute; top: 63px; left: 627px; display: flex; gap: 9px; }
  .social span { width: 30px; height: 30px; border-radius: 50%; background: var(--green); display: block; }

  /* Icon nav band */
  .dash-nav {
    position: absolute; left: 0; top: 101px; width: 750px; height: 135px;
    background: linear-gradient(var(--band-top), var(--band-bottom));
  }
  .dash-item { position: absolute; top: 29px; width: 90px; margin-left: -45px; text-align: center; font-size: 11.5px; line-height: 1.05; color: var(--ink-dark); }
  .dash-icon {
    width: 62px; height: 62px; margin: 0 auto 7px; border-radius: 50%;
    background: linear-gradient(#ffffff, #d9d9d9);
    box-shadow: 0 2px 3px rgba(0,0,0,0.25);
    display: flex; align-items: center; justify-content: center; position: relative;
  }
  .dash-icon .glyph-fill { width: 36px; height: 36px; border-radius: 50%; background: linear-gradient(#6a6f6c, #4b504d); }
  .dash-item--active { color: var(--active-blue); }
  .dash-item--active .glyph-fill { background: linear-gradient(#2f86d6, #1a6fc4); }
  .badge {
    position: absolute; right: -6px; top: 2px; min-width: 28px; height: 20px; border-radius: 5px;
    background: var(--badge-red); color: var(--white); font-size: 11px; line-height: 20px; text-align: center;
  }
  .active-notch {
    position: absolute; left: 503px; top: 127px; width: 0; height: 0;
    border-left: 8px solid transparent; border-right: 8px solid transparent; border-bottom: 8px solid var(--white);
  }

  /* Sign-in panel */
  .account-panel { position: absolute; left: 17px; top: 262px; width: 712px; height: 311px; background: var(--panel); border-radius: 8px; }
  .panel-tab {
    position: absolute; top: 16px; height: 48px; border-radius: 7px 7px 0 0;
    color: var(--white); font-size: 19px; line-height: 50px; text-align: center;
  }
  .panel-tab--signin { left: 26px; width: 109px; background: var(--green); }
  .panel-tab--register { left: 139px; width: 124px; background: var(--grey-tab); }
  .form-frame { position: absolute; left: 10px; top: 63px; width: 688px; height: 238px; background: var(--green); border-radius: 8px; }
  .form-card { position: absolute; left: 18px; top: 19px; width: 649px; height: 202px; background: var(--white); border-radius: 8px; }

  .field-label { position: absolute; left: 0; width: 148px; text-align: right; font-size: 19px; font-weight: 700; color: var(--ink); }
  .field-input { position: absolute; left: 170px; width: 310px; height: 40px; background: var(--field); border: 1px solid var(--field-border); border-radius: 9px; }
  .label-email { top: 26px; } .input-email { top: 20px; }
  .label-password { top: 71px; } .input-password { top: 65px; }

  .remember { position: absolute; left: 173px; top: 114px; display: flex; align-items: center; gap: 9px; font-size: 11.5px; font-weight: 700; }
  .remember .box { width: 15px; height: 15px; background: var(--field); border: 1px solid var(--field-border); border-radius: 2px; }
  .forgot { position: absolute; left: 315px; top: 115px; font-size: 10.5px; font-weight: 700; color: var(--link-red); }

  .sign-in-button {
    position: absolute; left: 170px; top: 141px; width: 139px; height: 38px; border-radius: 8px;
    background: linear-gradient(#f4f4f4, #cdcdcd); box-shadow: 0 1px 2px rgba(0,0,0,0.2);
    font-size: 19px; font-weight: 700; color: var(--ink); text-align: center; line-height: 37px;
  }
</style>
</head>
<body>
<div class="app">
  <header class="site-header">
    <div class="brand">
      <span class="brand-square"></span>
      <span class="brand-name">VantiQor</span>
    </div>

    <div class="main-tab main-tab--order">
      <svg width="34" height="24" viewBox="0 0 34 24" aria-hidden="true">
        <rect x="5" y="1" width="24" height="17" rx="2" fill="#a8a8a8"/>
        <rect x="1" y="19" width="32" height="4" rx="1" fill="#a8a8a8"/>
      </svg>
      ORDER A TEST
    </div>
    <div class="main-tab main-tab--dashboard">
      <svg width="28" height="26" viewBox="0 0 28 26" aria-hidden="true">
        <rect x="8" y="1" width="18" height="15" fill="none" stroke="#7cc036" stroke-width="2.5"/>
        <rect x="2" y="8" width="18" height="16" fill="#ececec" stroke="#7cc036" stroke-width="2.5"/>
      </svg>
      DASHBOARD
    </div>

    <div class="social" aria-label="Social links">
      <span></span><span></span><span></span>
    </div>
  </header>

  <nav class="dash-nav">
    <div class="dash-item" style="left:46px">
      <div class="dash-icon">
        <svg width="36" height="36" viewBox="0 0 36 36" aria-hidden="true">
          <rect x="3" y="4" width="30" height="22" rx="2" fill="#4f5451"/>
          <rect x="6" y="7" width="24" height="16" fill="#e4e4e4"/>
          <polyline points="7,15 13,15 15,10 18,20 21,13 23,15 29,15" fill="none" stroke="#4f5451" stroke-width="1.8"/>
          <rect x="15" y="26" width="6" height="4" fill="#4f5451"/>
          <rect x="10" y="30" width="16" height="3" fill="#4f5451"/>
        </svg>
      </div>My<br>Confirmation
    </div>
    <div class="dash-item" style="left:140px">
      <div class="dash-icon"><span class="glyph-fill" role="img" aria-label="Microscope icon"></span></div>My<br>Nearest Lab
    </div>
    <div class="dash-item" style="left:233px">
      <div class="dash-icon"><span class="glyph-fill" role="img" aria-label="DNA strand icon"></span></div>My Orders
    </div>
    <div class="dash-item" style="left:327px">
      <div class="dash-icon">
        <svg width="36" height="36" viewBox="0 0 36 36" aria-hidden="true">
          <rect x="6" y="4" width="24" height="30" rx="2" fill="#4f5451"/>
          <rect x="9" y="8" width="18" height="23" fill="#e4e4e4"/>
          <rect x="13" y="2" width="10" height="5" rx="1" fill="#4f5451"/>
          <polyline points="10,20 14,20 16,15 19,25 21,18 23,20 26,20" fill="none" stroke="#4f5451" stroke-width="1.6"/>
        </svg>
      </div>My Results
    </div>
    <div class="dash-item" style="left:419px">
      <div class="dash-icon">
        <svg width="36" height="36" viewBox="0 0 36 36" aria-hidden="true">
          <rect x="6" y="4" width="24" height="30" rx="2" fill="#4f5451"/>
          <rect x="9" y="8" width="18" height="23" fill="#e4e4e4"/>
          <rect x="13" y="2" width="10" height="5" rx="1" fill="#4f5451"/>
          <g fill="#4f5451">
            <rect x="11" y="12" width="3" height="2"/><rect x="16" y="12" width="9" height="2"/>
            <rect x="11" y="17" width="3" height="2"/><rect x="16" y="17" width="9" height="2"/>
            <rect x="11" y="22" width="3" height="2"/><rect x="16" y="22" width="9" height="2"/>
            <rect x="11" y="27" width="3" height="2"/><rect x="16" y="27" width="9" height="2"/>
          </g>
        </svg>
      </div>My Receipts
    </div>
    <div class="dash-item dash-item--active" style="left:511px">
      <div class="dash-icon"><span class="glyph-fill" role="img" aria-label="Account profile icon"></span></div>My Account
    </div>
    <div class="dash-item" style="left:606px">
      <div class="dash-icon">
        <svg width="38" height="30" viewBox="0 0 38 30" aria-hidden="true">
          <rect x="1" y="3" width="36" height="24" fill="#4f5451"/>
          <polyline points="2,4 19,18 36,4" fill="none" stroke="#e4e4e4" stroke-width="2"/>
          <polyline points="2,26 14,14 M36,26 24,14" fill="none" stroke="#e4e4e4" stroke-width="1.5"/>
        </svg>
        <span class="badge">2</span>
      </div>My Inbox
    </div>
    <div class="dash-item" style="left:700px">
      <div class="dash-icon"><span class="glyph-fill" role="img" aria-label="Customer support agent icon"></span></div>Contact Us
    </div>
    <span class="active-notch"></span>
  </nav>

  <section class="account-panel">
    <div class="panel-tab panel-tab--signin">SIGN IN</div>
    <div class="panel-tab panel-tab--register">REGISTER</div>
    <div class="form-frame">
      <form class="form-card">
        <label class="field-label label-email">EMAIL</label>
        <div class="field-input input-email"></div>
        <label class="field-label label-password">PASSWORD</label>
        <div class="field-input input-password"></div>
        <div class="remember"><span class="box"></span>Remember Me</div>
        <span class="forgot">Forgot you Password?</span>
        <div class="sign-in-button">sign in</div>
      </form>
    </div>
  </section>
</div>
</body>
</html>
```